Freelance business trainer needs a new business card

My business is called Brontlearn. I provide training in the workplace on management, coaching and mentoring, and customer service topics for a variety of businesses, colleges and private training providers, and teach on management programs. I need a professional but eye catching business card. Business colours grey and orange. My name Marion Tadwick; Tel 07382 415067; email mtadwick@brontlearn.co.uk; website www.brontlearn.co.uk.
Happy to have some sort of logo on front and details on back or all on one side
Target Market(s)
SME businesses and colleges - workshops i run are for adults in the workplace
Industry/Entity Type
Training
Look and feel

```html
<!DOCTYPE html>
<html lang="en">
<head>
<meta charset="utf-8">
<title>Brontlearn – Business Card</title>
<link href="https://fonts.googleapis.com/css2?family=Montserrat:wght@400;500;700&display=swap" rel="stylesheet">
<style>
  :root {
    --orange: #f7931e;
    --orange-soft: #f9a74a;
    --grey: #6d6d6d;
    --grey-dark: #2e2e2e;
    --grey-mid: #8a8a8a;
    --white: #ffffff;
    --backdrop: #d9dadc;
    --font: "Montserrat", Arial, sans-serif;
  }
  * { margin: 0; padding: 0; box-sizing: border-box; }
  html, body { width: 1200px; height: 800px; overflow: hidden; }
  body { background: var(--backdrop); font-family: var(--font); position: relative; }

  .card {
    position: absolute;
    top: 245px;
    width: 540px;
    height: 310px;
    border-radius: 24px;
    overflow: hidden;
  }
  .circle { position: absolute; border-radius: 50%; }

  /* Front */
  .card-front { left: 50px; background: var(--orange); }
  .card-front .circle-top { width: 300px; height: 300px; left: 210px; top: -150px; background: rgba(255,255,255,0.15); }
  .card-front .circle-mid { width: 300px; height: 300px; left: 60px; top: 20px; background: rgba(255,255,255,0.10); }
  .card-front .base-band { position: absolute; left: 0; right: 0; bottom: 0; height: 30px; background: var(--grey-dark); border-top: 6px solid var(--grey-mid); }
  .card-front .brand {
    position: absolute; left: 0; right: 0; top: 88px; text-align: center;
    font-size: 62px; font-weight: 500; color: var(--white); letter-spacing: 1px;
  }
  .card-front .website {
    position: absolute; left: 0; right: 0; top: 186px; text-align: center;
    font-size: 15px; letter-spacing: 4px; color: var(--white);
  }

  /* Back */
  .card-back { left: 610px; background: var(--grey); }
  .card-back .circle-low { width: 250px; height: 250px; left: 210px; top: 150px; background: rgba(255,255,255,0.07); }
  .card-back .circle-right { width: 230px; height: 230px; left: 420px; top: 145px; background: rgba(255,255,255,0.06); }
  .card-back .top-band { position: absolute; left: 0; right: 0; top: 0; height: 44px; background: var(--grey-dark); border-bottom: 4px solid var(--orange); }
  .card-back .website {
    position: absolute; right: 26px; top: 13px; font-size: 13px; letter-spacing: 3px; color: var(--orange);
  }
  .card-back .foot-accent { position: absolute; right: 0; bottom: 12px; width: 120px; height: 4px; background: var(--orange); }
  .card-back .foot-band { position: absolute; right: 0; bottom: 0; width: 120px; height: 12px; background: var(--grey-dark); }

  .person { position: absolute; left: 32px; top: 72px; color: var(--white); }
  .person .name { font-size: 20px; font-weight: 700; color: var(--orange); letter-spacing: 0.5px; text-transform: uppercase; }
  .person .role { font-size: 12px; margin-top: 4px; }
  .person .quals { font-size: 12px; margin-top: 2px; }
  .contact { list-style: none; margin-top: 14px; font-size: 14px; }
  .contact li { margin-bottom: 3px; }
  .contact .label { color: var(--orange); font-size: 11px; margin-right: 6px; }

  .card-back .brand {
    position: absolute; right: 36px; top: 132px; font-size: 42px; font-weight: 500; color: var(--white);
  }
  .address { position: absolute; left: 250px; top: 208px; font-size: 14px; line-height: 1.3; color: var(--white); font-style: normal; }
</style>
</head>
<body>
  <section class="card card-front">
    <div class="circle circle-top"></div>
    <div class="circle circle-mid"></div>
    <div class="brand">Brontlearn</div>
    <div class="website">www.brontlearn.co.uk</div>
    <div class="base-band"></div>
  </section>

  <section class="card card-back">
    <div class="circle circle-low"></div>
    <div class="circle circle-right"></div>
    <div class="top-band"><span class="website">www.brontlearn.co.uk</span></div>
    <div class="person">
      <div class="name">Marion Tadwick</div>
      <div class="role">Owner/Lead Trainer</div>
      <div class="quals">MCMI, MIFL, CertEd, PGCCM, TIOSH</div>
      <ul class="contact">
        <li><span class="label">[T]</span>07382 415067</li>
        <li><span class="label">[E]</span>mtadwick@brontlearn.co.uk</li>
      </ul>
    </div>
    <div class="brand">Brontlearn</div>
    <address class="address">Elmbrook House<br>Fennick Lane<br>Harwell<br>RG31 4QT</address>
    <div class="foot-accent"></div>
    <div class="foot-band"></div>
  </section>
</body>
</html>
```